RW Framewell Inc Business cards

We need business cards using our existing logo but slightly modified. Right now the logo says RW Loadbearing Masonry. We want to keep the RW part of the design, but replace the Structural Concrete portion with "FRAMEWELL". Please see the attached file.
Ideally this would be a blank template so we can add Different Names, titles, and phone numbers later.
On the one side we want only the logo and on the other side the detail. I'm attaching an example for you to see.
Please reach out with any other questions. Our address and other details will be given out once we find a design we like.

Target Market(s)

Construction Industry

```html
<!DOCTYPE html>
<html lang="en">
<head>
<meta charset="utf-8">
<title>RW Framewell Inc – Business Cards</title>
<link href="https://fonts.googleapis.com/css2?family=Archivo+Black&family=Roboto:wght@400&family=Roboto+Condensed:wght@700&display=swap" rel="stylesheet">
<style>
  :root {
    --brand-blue: #1a75bc;
    --brand-grey: #808184;
    --text-grey: #58595b;
    --rule-grey: #9d9ea0;
    --card-white: #ffffff;
    --backdrop: #a3a3a3;
  }
  html, body {
    margin: 0;
    padding: 0;
    width: 1200px;
    height: 1200px;
    overflow: hidden;
    background: var(--backdrop);
  }
  .canvas {
    position: relative;
    width: 1200px;
    height: 1200px;
  }
  .card {
    position: absolute;
    top: 303px;
    width: 368px;
    height: 594px;
    overflow: hidden;
  }

  /* Front: logo side */
  .card--front {
    left: 200px;
    background: var(--brand-grey);
  }
  .front-band {
    position: absolute;
    left: 0;
    top: 0;
    width: 100%;
    height: 366px;
    background: var(--brand-blue);
  }
  .front-name {
    position: absolute;
    left: 0;
    right: 0;
    top: 236px;
    margin: 0;
    text-align: center;
    font-family: "Archivo Black", sans-serif;
    font-size: 50px;
    line-height: 58px;
    color: var(--card-white);
    letter-spacing: 1px;
  }
  .front-web {
    position: absolute;
    left: 0;
    right: 0;
    top: 528px;
    margin: 0;
    text-align: center;
    font-family: "Roboto Condensed", sans-serif;
    font-weight: 700;
    font-size: 18px;
    color: var(--card-white);
  }

  /* Back: detail side */
  .card--back {
    left: 599px;
    width: 365px;
    background: var(--card-white);
  }
  .back-name {
    position: absolute;
    left: 0;
    right: 0;
    top: 112px;
    margin: 0;
    text-align: center;
    font-family: "Archivo Black", sans-serif;
    font-size: 44px;
    line-height: 52px;
    color: var(--brand-blue);
    letter-spacing: 1px;
  }
  .person {
    position: absolute;
    left: 0;
    right: 0;
    top: 392px;
    text-align: center;
  }
  .person-name {
    margin: 0;
    font-family: "Archivo Black", sans-serif;
    font-size: 21px;
    line-height: 26px;
    color: var(--brand-blue);
    letter-spacing: 0.5px;
  }
  .person-title {
    margin: 0;
    font-family: "Roboto", sans-serif;
    font-size: 17px;
    line-height: 20px;
    color: var(--text-grey);
  }
  .icon-row {
    position: absolute;
    left: 0;
    right: 0;
    top: 452px;
    display: flex;
    justify-content: center;
    align-items: center;
    gap: 4px;
  }
  .icon-rule {
    width: 52px;
    height: 1px;
    background: var(--rule-grey);
    margin: 0 3px;
  }
  .icon {
    width: 25px;
    height: 25px;
    display: block;
  }
  .contact {
    position: absolute;
    left: 0;
    right: 0;
    top: 488px;
    margin: 0;
    text-align: center;
    font-family: "Roboto", sans-serif;
    font-size: 17px;
    line-height: 22px;
    color: var(--text-grey);
    font-style: normal;
  }
</style>
</head>
<body>
<main class="canvas">

  <section class="card card--front" aria-label="Card front">
    <div class="front-band"></div>
    <p class="front-name">RW<br>FRAMEWELL</p>
    <p class="front-web">WWW.RWFRAMEWELL.COM</p>
  </section>

  <section class="card card--back" aria-label="Card back">
    <p class="back-name">RW<br>FRAMEWELL</p>

    <div class="person">
      <p class="person-name">DANIEL HARTWELL</p>
      <p class="person-title">Managing Director</p>
    </div>

    <div class="icon-row">
      <span class="icon-rule"></span>
      <svg class="icon" viewBox="0 0 25 25" aria-label="Phone">
        <rect width="25" height="25" rx="3" fill="var(--brand-blue)"/>
        <path d="M6 10c0-2 3-3 6.5-3S19 8 19 10v1h-3v-1.5h-7V11H6z" fill="#fff"/>
        <rect x="8" y="12" width="9" height="6" rx="1" fill="#fff"/>
      </svg>
      <svg class="icon" viewBox="0 0 25 25" aria-label="Email">
        <rect width="25" height="25" rx="3" fill="var(--brand-blue)"/>
        <rect x="6" y="8" width="13" height="9" fill="none" stroke="#fff" stroke-width="1.3"/>
        <path d="M6 8l6.5 5L19 8M6 17l5-4.5M19 17l-5-4.5" fill="none" stroke="#fff" stroke-width="1.1"/>
      </svg>
      <svg class="icon" viewBox="0 0 25 25" aria-label="Website">
        <rect width="25" height="25" rx="3" fill="var(--brand-blue)"/>
        <circle cx="12.5" cy="12.5" r="6.5" fill="#fff"/>
        <path d="M9 9.5c1.5-1 3 0 3.5 1.5s-1 2-2.5 2.5S9 16 9.5 17.5M14.5 7.5c1 1.5 2.5 2 3.5 3" fill="none" stroke="var(--brand-blue)" stroke-width="1.3"/>
      </svg>
      <span class="icon-rule"></span>
    </div>

    <address class="contact">
      044-987 654 321<br>
      info@rwframewell.com<br>
      www.rwframewell.com
    </address>
  </section>

</main>
</body>
</html>
```